Business card for Internet Marketing Consultant

Simple - need a nice business card design using the logo elements and colors. Keywords: Progressive, professional, stylish, minimalist. Please use the nb as part of the design.

Info for card:

Brendan Okafor
Internet Marketing Strategist
Phone: (520) 555-0148
Email: brendan@northbeamgrowth.com
Address: 2193 W. Larkmoor Ave., Ste. 118
Tucson, Arizona 85710

Website: www.northbeamgrowth.com

Industry/Entity Type

Business

Font styles to use
Sans Serif

```html
<!DOCTYPE html>
<html lang="en">
<head>
<meta charset="utf-8">
<title>Northbeam Growth – Business Card</title>
<link rel="stylesheet" href="https://fonts.googleapis.com/css2?family=Jost:wght@300;400;600&family=Arimo:wght@400;700&display=swap">
<style>
  :root {
    --brand-blue: #2f6bbd;
    --brand-green: #5cb865;
    --ink: #1f1f1f;
    --muted: #6b6b6b;
    --paper: #ffffff;
    --backdrop: #e9e7e3;
  }
  * { box-sizing: border-box; margin: 0; padding: 0; }
  html, body { width: 1200px; height: 900px; overflow: hidden; }
  body {
    background: var(--backdrop);
    display: flex;
    flex-direction: column;
    align-items: center;
    justify-content: center;
    gap: 40px;
    font-family: "Arimo", Arial, sans-serif;
  }
  .card {
    position: relative;
    width: 700px;
    height: 400px;
    background: var(--paper);
    overflow: hidden;
    box-shadow: 0 6px 18px rgba(0,0,0,0.15);
  }

  /* Wordmark */
  .wordmark { display: flex; align-items: center; gap: 14px; }
  .wordmark-square {
    width: 44px; height: 44px;
    background: var(--brand-green);
    flex: none;
  }
  .wordmark-text { display: flex; flex-direction: column; }
  .wordmark-name {
    font-family: "Jost", sans-serif;
    font-weight: 600;
    color: var(--brand-blue);
    line-height: 1;
  }
  .wordmark-tagline {
    font-family: "Jost", sans-serif;
    font-weight: 300;
    color: var(--muted);
    text-transform: uppercase;
    letter-spacing: 0.28em;
    margin-top: 6px;
  }

  /* Back of card */
  .card-back {
    display: flex;
    flex-direction: column;
    align-items: center;
    justify-content: center;
    gap: 22px;
  }
  .card-back .wordmark-name { font-size: 50px; }
  .card-back .wordmark-tagline { font-size: 15px; }
  .address { font-size: 17px; color: var(--ink); }

  /* Front of card */
  .card-front .wordmark {
    position: absolute;
    left: 40px; top: 56px;
  }
  .card-front .wordmark-name { font-size: 46px; }
  .card-front .wordmark-tagline { font-size: 14px; }

  .contact-band {
    position: absolute;
    left: 0; bottom: 0;
    width: 560px; height: 190px;
    background: var(--brand-blue);
    color: #fff;
    padding: 26px 40px;
  }
  .accent-square {
    position: absolute;
    right: 0; bottom: 0;
    width: 140px; height: 250px;
    background: var(--brand-green);
  }
  .person-name { font-size: 22px; font-weight: 700; }
  .person-title { font-size: 13px; margin-top: 3px; margin-bottom: 16px; }
  .contact-list { list-style: none; display: flex; flex-direction: column; gap: 9px; }
  .contact-item { display: flex; align-items: center; gap: 10px; font-size: 14px; }
  .contact-icon {
    width: 18px; height: 18px;
    background: #fff;
    border-radius: 3px;
    display: flex; align-items: center; justify-content: center;
    flex: none;
  }
</style>
</head>
<body>

  <section class="card card-back">
    <div class="wordmark">
      <span class="wordmark-square"></span>
      <div class="wordmark-text">
        <span class="wordmark-name">northbeamgrowth</span>
        <span class="wordmark-tagline">Internet Marketing Strategies</span>
      </div>
    </div>
    <p class="address">2193 W. Larkmoor Ave., Ste. 118 Tucson, Arizona 85710</p>
  </section>

  <section class="card card-front">
    <div class="wordmark">
      <span class="wordmark-square"></span>
      <div class="wordmark-text">
        <span class="wordmark-name">northbeamgrowth</span>
        <span class="wordmark-tagline">Internet Marketing Strategies</span>
      </div>
    </div>

    <div class="accent-square"></div>

    <div class="contact-band">
      <p class="person-name">Brendan Okafor</p>
      <p class="person-title">Internet Marketing Strategist</p>
      <ul class="contact-list">
        <li class="contact-item">
          <span class="contact-icon">
            <svg width="12" height="12" viewBox="0 0 24 24"><path fill="#2f6bbd" d="M6.6 10.8a15 15 0 0 0 6.6 6.6l2.2-2.2c.3-.3.7-.4 1-.2 1.1.4 2.3.6 3.6.6.6 0 1 .4 1 1V20c0 .6-.4 1-1 1A17 17 0 0 1 3 4c0-.6.4-1 1-1h3.5c.6 0 1 .4 1 1 0 1.3.2 2.5.6 3.6.1.3 0 .7-.2 1z"/></svg>
          </span>
          (520) 555-0148
        </li>
        <li class="contact-item">
          <span class="contact-icon">
            <svg width="12" height="12" viewBox="0 0 24 24"><rect x="2" y="5" width="20" height="14" rx="1" fill="none" stroke="#2f6bbd" stroke-width="2.4"/><path d="M2 6l10 7 10-7" fill="none" stroke="#2f6bbd" stroke-width="2.4"/></svg>
          </span>
          brendan@northbeamgrowth.com
        </li>
        <li class="contact-item">
          <span class="contact-icon">
            <svg width="12" height="12" viewBox="0 0 24 24"><circle cx="12" cy="12" r="9" fill="none" stroke="#2f6bbd" stroke-width="2.2"/><path d="M3 12h18M12 3c3 3 3 15 0 18M12 3c-3 3-3 15 0 18" fill="none" stroke="#2f6bbd" stroke-width="1.8"/></svg>
          </span>
          www.northbeamgrowth.com
        </li>
      </ul>
    </div>
  </section>

</body>
</html>
```